VOMRA Pty Ltd Business Card

Looking for a simple yet eye-catching double-sided business card design using my company logo on one side and contact details on the other.

Target Market(s)

Government

Industry/Entity Type

Communication Systems Engineering

Contact Information for Business Card

VOMRA Pty Ltd

Requirements
Nice to have
• Would be great to have a QR code so details can be scanned into contacts

```html
<!DOCTYPE html>
<html lang="en">
<head>
<meta charset="utf-8">
<title>VOMRA Pty Ltd Business Card</title>
<link rel="stylesheet" href="https://fonts.googleapis.com/css2?family=Montserrat:wght@400;500;700&display=swap">
<style>
  :root {
    --page-bg: #d9d9d9;
    --card-light: #6a7278;
    --card-dark: #323b42;
    --ink: #f4f2f0;
    --ink-soft: #e2e2e2;
  }
  * { margin: 0; padding: 0; box-sizing: border-box; }
  html, body {
    width: 1200px;
    height: 1200px;
    overflow: hidden;
    background: var(--page-bg);
    font-family: "Montserrat", sans-serif;
  }
  .sheet {
    width: 1200px;
    height: 1200px;
    display: flex;
    flex-direction: column;
    align-items: center;
    justify-content: center;
    gap: 60px;
  }
  .card {
    position: relative;
    width: 840px;
    height: 480px;
    border-radius: 30px;
    background: linear-gradient(110deg, var(--card-light) 0%, var(--card-dark) 60%, var(--card-dark) 100%);
    color: var(--ink);
    box-shadow: 0 10px 24px rgba(0,0,0,0.18);
  }
  .brand {
    display: flex;
    align-items: center;
    gap: 26px;
    font-weight: 500;
    letter-spacing: 0.02em;
    color: var(--ink);
  }
  .brand-dot {
    border-radius: 50%;
    border: 3px solid var(--ink);
  }
  /* Front */
  .card-front {
    display: flex;
    align-items: center;
    justify-content: center;
  }
  .card-front .brand { font-size: 124px; }
  .card-front .brand-dot { width: 110px; height: 110px; }

  /* Back */
  .card-back .brand {
    position: absolute;
    top: 58px;
    left: 50%;
    transform: translateX(-50%);
    font-size: 76px;
    gap: 18px;
  }
  .card-back .brand-dot { width: 70px; height: 70px; border-width: 2px; }

  .details {
    position: absolute;
    top: 212px;
    left: 0;
    right: 0;
    display: flex;
    justify-content: center;
    align-items: center;
    gap: 34px;
  }
  .person { text-align: right; }
  .person-name {
    font-weight: 700;
    font-size: 34px;
    color: var(--ink);
  }
  .person-role {
    font-size: 22px;
    font-weight: 400;
    color: var(--ink-soft);
    margin-top: 4px;
  }
  .divider {
    width: 2px;
    height: 104px;
    background: var(--ink);
  }
  .contacts {
    list-style: none;
    display: flex;
    flex-direction: column;
    gap: 8px;
    font-size: 22px;
    color: var(--ink-soft);
  }
  .contacts li { display: flex; align-items: center; gap: 14px; }
  .contacts svg { width: 18px; height: 18px; fill: var(--ink); flex: none; }
  .address {
    position: absolute;
    bottom: 58px;
    left: 0;
    right: 0;
    text-align: center;
    font-size: 23px;
    color: var(--ink-soft);
    letter-spacing: 0.01em;
  }
</style>
</head>
<body>
<main class="sheet">
  <section class="card card-front" aria-label="Card front">
    <div class="brand"><span class="brand-dot"></span><span class="brand-name">VOMRA</span></div>
  </section>

  <section class="card card-back" aria-label="Card back">
    <div class="brand"><span class="brand-dot"></span><span class="brand-name">VOMRA</span></div>

    <div class="details">
      <div class="person">
        <div class="person-name">Dalton Reeve</div>
        <div class="person-role">Founder &amp; Director</div>
      </div>
      <div class="divider"></div>
      <ul class="contacts">
        <li>
          <svg viewBox="0 0 24 24" aria-hidden="true"><path d="M6.6 10.8a15.1 15.1 0 0 0 6.6 6.6l2.2-2.2c.3-.3.7-.4 1-.2 1.1.4 2.3.6 3.6.6.6 0 1 .4 1 1V20c0 .6-.4 1-1 1A17 17 0 0 1 3 4c0-.6.4-1 1-1h3.5c.6 0 1 .4 1 1 0 1.3.2 2.5.6 3.6.1.3 0 .7-.2 1z"/></svg>
          <span>(402)-555-0147</span>
        </li>
        <li>
          <svg viewBox="0 0 24 24" aria-hidden="true"><path d="M2 5h20v14H2z M2 5l10 8 10-8" fill="none" stroke="#f4f2f0" stroke-width="0"/><path d="M2 6.5V19h20V6.5l-10 7.5z M2.8 5h18.4L12 11.9z"/></svg>
          <span>admin@vomra.com.au</span>
        </li>
        <li>
          <svg viewBox="0 0 24 24" aria-hidden="true"><path d="M12 2a10 10 0 1 0 0 20 10 10 0 0 0 0-20zm6.9 9h-3a15 15 0 0 0-1.3-6.1A8 8 0 0 1 18.9 11zM12 4.1c.9 1.3 1.8 3.7 1.9 6.9h-3.8c.1-3.2 1-5.6 1.9-6.9zM9.4 4.9A15 15 0 0 0 8.1 11h-3a8 8 0 0 1 4.3-6.1zM5.1 13h3a15 15 0 0 0 1.3 6.1A8 8 0 0 1 5.1 13zM12 19.9c-.9-1.3-1.8-3.7-1.9-6.9h3.8c-.1 3.2-1 5.6-1.9 6.9zm2.6-.8a15 15 0 0 0 1.3-6.1h3a8 8 0 0 1-4.3 6.1z"/></svg>
          <span>www.vomra.com.au</span>
        </li>
      </ul>
    </div>

    <p class="address">42-44 Harper Lane Redfield NSW 2071 Australia</p>
  </section>
</main>
</body>
</html>
```